Investment company needing business card

We are wanting a business card which looks sharp and easy on the eye. We are thinking of having a business card with the logo embossed on it, to really make it stand out. We will only have a small amount of information of the business card, person's name, position, email address and phone number

Contact Information for Business Card

Danielle Frost
Executive Assistant
+64 21 473 5162
danielf@harwickpartners.co.nz

Requirements
Must have
• Embossed logo
Should not have
• Not to be busy

```html
<!DOCTYPE html>
<html lang="en">
<head>
<meta charset="utf-8">
<title>Harwick Partners – Business Card</title>
<link href="https://fonts.googleapis.com/css2?family=Michroma&family=Open+Sans:wght@400;600&display=swap" rel="stylesheet">
<style>
  :root {
    --backdrop: #e6e4e1;
    --card-dark: #141414;
    --card-mid: #222222;
    --brand-green: #2fbf7c;
    --steel-grey: #8a8a8a;
    --text-light: #e8e8e8;
    --text-soft: #b9b9b9;
    --emboss-face: #1d1d1d;
  }
  * { margin: 0; padding: 0; box-sizing: border-box; }
  html, body { width: 1200px; height: 960px; overflow: hidden; }
  body {
    background: var(--backdrop);
    font-family: "Open Sans", Arial, sans-serif;
    position: relative;
  }
  .card {
    position: absolute;
    left: 220px;
    width: 760px;
    height: 420px;
    border-radius: 6px;
    background:
      repeating-linear-gradient(90deg, rgba(255,255,255,0.018) 0 1px, transparent 1px 3px),
      linear-gradient(160deg, var(--card-mid) 0%, var(--card-dark) 70%);
    box-shadow: 0 14px 30px rgba(0,0,0,0.28);
    overflow: hidden;
  }
  .card--front { top: 40px; }
  .card--back { top: 500px; }

  .wordmark {
    display: flex;
    align-items: center;
    gap: 18px;
    font-family: "Michroma", "Arial Black", sans-serif;
    color: var(--brand-green);
    font-size: 34px;
    letter-spacing: 1px;
    white-space: nowrap;
  }
  .wordmark__square {
    width: 46px; height: 46px;
    background: var(--brand-green);
    border-radius: 4px;
  }
  .card--front .wordmark {
    position: absolute;
    top: 130px; left: 0; right: 0;
    justify-content: center;
  }
  .card--front .web-address {
    position: absolute;
    top: 240px; left: 0; right: 0;
    text-align: center;
    color: var(--text-light);
    font-size: 22px;
    letter-spacing: 2px;
  }

  .card--back .wordmark {
    position: absolute;
    top: 62px; left: 48px;
    font-size: 30px;
  }
  .emboss-block {
    position: absolute;
    right: 50px; top: 130px;
    width: 190px; height: 190px;
    border-radius: 18px;
    background: var(--emboss-face);
    box-shadow: inset 2px 2px 3px rgba(255,255,255,0.08), inset -3px -3px 6px rgba(0,0,0,0.6), 4px 5px 8px rgba(0,0,0,0.5);
  }
  .person {
    position: absolute;
    left: 50px; top: 190px;
  }
  .person__name {
    font-family: "Michroma", "Arial Black", sans-serif;
    color: var(--brand-green);
    font-size: 21px;
    letter-spacing: 1px;
  }
  .person__role {
    font-family: "Michroma", "Arial Black", sans-serif;
    color: var(--text-soft);
    font-size: 15px;
    margin-top: 8px;
    letter-spacing: 1px;
  }
  .contact-list {
    position: absolute;
    left: 50px; top: 290px;
    list-style: none;
  }
  .contact-list li {
    display: flex;
    align-items: center;
    gap: 12px;
    color: var(--text-light);
    font-size: 17px;
    line-height: 32px;
  }
  .contact-list svg { width: 16px; height: 16px; flex: none; }
</style>
</head>
<body>
  <section class="card card--front">
    <div class="wordmark"><span class="wordmark__square"></span>HARWICK PARTNERS</div>
    <p class="web-address">www.harwickpartners.co.nz</p>
  </section>

  <section class="card card--back">
    <div class="wordmark"><span class="wordmark__square"></span>HARWICK PARTNERS</div>
    <div class="emboss-block"></div>
    <div class="person">
      <p class="person__name">DANIELLE FROST</p>
      <p class="person__role">EXECUTIVE ASSISTANT</p>
    </div>
    <ul class="contact-list">
      <li>
        <svg viewBox="0 0 16 16"><path fill="#2fbf7c" d="M3.5 1.5l2.5 0 1 3.5-1.7 1.2a8 8 0 0 0 4.5 4.5L11 9l3.5 1v2.5c0 1-1 2-2 2A11 11 0 0 1 1.5 3.5c0-1 1-2 2-2z"/></svg>
        +64 21 473 5162
      </li>
      <li>
        <svg viewBox="0 0 16 16"><rect x="1" y="3" width="14" height="10" rx="1.5" fill="#2fbf7c"/><path d="M1.5 4l6.5 5 6.5-5" stroke="#141414" stroke-width="1.4" fill="none"/></svg>
        danielf@harwickpartners.co.nz
      </li>
      <li>
        <svg viewBox="0 0 16 16" fill="none" stroke="#2fbf7c" stroke-width="1.4"><circle cx="8" cy="8" r="6.5"/><ellipse cx="8" cy="8" rx="3" ry="6.5"/><path d="M1.5 8h13"/></svg>
        www.harwickpartners.co.nz
      </li>
    </ul>
  </section>
</body>
</html>
```